Velora Entertainment

Logo for business card design

Target Market(s)

potential film investors and screenwriters

Industry/Entity Type

Business

Contact Information for Business Card

as shown, website here is a placeholder position

Requirements
Must have
• great visual appeal
Nice to have
• harmony of colors; must evoke spirit of
• U.S.-China cooperation

```html
<!DOCTYPE html>
<html lang="en">
<head>
<meta charset="utf-8">
<title>Velora Entertainment – Business Card</title>
<link href="https://fonts.googleapis.com/css2?family=Open+Sans:wght@400;600;700;800&display=swap" rel="stylesheet">
<style>
  :root {
    --page-bg: #7e7f81;
    --card-front: #ececef;
    --card-back: #8c8d90;
    --brand-red: #c0090f;
    --brand-yellow: #dcbc00;
    --brand-navy: #0e0e6e;
    --ink-white: #ffffff;
  }
  * { margin: 0; padding: 0; box-sizing: border-box; }
  html, body {
    width: 1105px;
    height: 1200px;
    overflow: hidden;
    background: var(--page-bg);
    font-family: "Open Sans", Arial, sans-serif;
  }
  .card {
    position: absolute;
    left: 182px;
    width: 747px;
    height: 426px;
    overflow: hidden;
  }
  .card--front { top: 119px; background: var(--card-front); }
  .card--back { top: 637px; background: var(--card-back); }

  .brand {
    position: absolute;
    display: flex;
    align-items: center;
    gap: 16px;
  }
  .brand__mark {
    width: 58px;
    height: 58px;
    background: var(--brand-red);
    flex: none;
  }
  .brand__name {
    font-weight: 800;
    font-size: 30px;
    line-height: 1.1;
    text-transform: uppercase;
    letter-spacing: 1px;
  }
  .card--front .brand { left: 46px; top: 78px; }
  .card--front .brand__name { color: var(--brand-navy); }
  .card--back .brand {
    left: 50%;
    top: 50%;
    transform: translate(-50%, -50%);
  }
  .card--back .brand__name { color: var(--ink-white); }

  .holder {
    position: absolute;
    right: 43px;
    top: 40px;
    text-align: right;
  }
  .holder__name {
    color: var(--brand-red);
    font-weight: 600;
    font-size: 25px;
    line-height: 1.2;
  }
  .holder__title {
    color: var(--brand-navy);
    font-size: 20px;
    line-height: 1.3;
  }

  .band {
    position: absolute;
    top: 277px;
    height: 149px;
  }
  .band--red { left: 0; width: 315px; background: var(--brand-red); }
  .band--yellow { left: 319px; width: 108px; background: var(--brand-yellow); }
  .band--navy { left: 431px; width: 316px; background: var(--brand-navy); }

  .contact-list {
    list-style: none;
    position: absolute;
    left: 44px;
    top: 34px;
    color: var(--ink-white);
    font-size: 19px;
    line-height: 28.5px;
  }
  .contact-list li { display: flex; align-items: center; gap: 10px; }
  .contact-list svg { width: 17px; height: 17px; fill: var(--ink-white); flex: none; }

  .address {
    position: absolute;
    right: 43px;
    top: 34px;
    text-align: right;
    color: var(--ink-white);
    font-size: 19px;
    line-height: 28.5px;
    font-style: normal;
  }
</style>
</head>
<body>

<section class="card card--front">
  <div class="brand">
    <span class="brand__mark"></span>
    <span class="brand__name">Velora<br>Entertainment</span>
  </div>

  <div class="holder">
    <p class="holder__name">Daniel Harper</p>
    <p class="holder__title">CEO/Founder</p>
  </div>

  <div class="band band--red">
    <ul class="contact-list">
      <li>
        <svg viewBox="0 0 24 24" aria-hidden="true"><path d="M6.6 10.8a15.1 15.1 0 0 0 6.6 6.6l2.2-2.2c.3-.3.7-.4 1-.2 1.1.4 2.3.6 3.6.6.6 0 1 .4 1 1V20c0 .6-.4 1-1 1A17 17 0 0 1 3 4c0-.6.4-1 1-1h3.5c.6 0 1 .4 1 1 0 1.3.2 2.5.6 3.6.1.3 0 .7-.2 1z"/></svg>
        512 380 4471
      </li>
      <li>
        <svg viewBox="0 0 24 24" aria-hidden="true"><path d="M7 1h10a2 2 0 0 1 2 2v18a2 2 0 0 1-2 2H7a2 2 0 0 1-2-2V3a2 2 0 0 1 2-2zm0 3v14h10V4zm5 15.5a1.2 1.2 0 1 0 0 2.4 1.2 1.2 0 0 0 0-2.4z"/></svg>
        512 209 6685
      </li>
      <li>
        <svg viewBox="0 0 24 24" aria-hidden="true"><path d="M2 5h20v14H2zm2 2v.4l8 5.2 8-5.2V7zm0 2.8V17h16V9.8l-8 5.2z"/></svg>
        hello@veloraent.com
      </li>
    </ul>
  </div>
  <div class="band band--yellow"></div>
  <div class="band band--navy">
    <address class="address">
      1420 Linden Court<br>
      Portland, Oregon 97205<br>
      www.veloraent.com
    </address>
  </div>
</section>

<section class="card card--back">
  <div class="brand">
    <span class="brand__mark"></span>
    <span class="brand__name">Velora<br>Entertainment</span>
  </div>
</section>

</body>
</html>
```